8'x8' Exhibit Backdrop for Healthcare Events focused on the 55 and older crowds

8X8 Backdrop for Exhibiting.

I also want a design for a 6' table skirt to include our logo on two sides and the logo with Hereditary Cancer Screening underneath on the front. I want the main message of Will You Give your Loved Ones The Information To Beat Cancer in Their Lives to be completely centered on the 8X8 backdrop. Hereditary Cancer Screening The Test You Take For Them in the top left corner and the purple box on the right hand side - just like the photo that has been uploaded below. I need High resolution photos around the backdrop but not so large that they overtake the main message.

Target Market(s)

55+ crowd living in Adult only communities. They have an active lifestyle

Industry/Entity Type

Healthcare

Other font styles liked:
• "The Test You Take For Them" is Comic Sans

Colors
0255a3
fbed22
ffffff

Requirements
Must have
• I am posting a photo of the exact backdrop I would like to see. There are red arrows showing where to move certain items. There is a space underneath the slogan WILL YOU GIVE YOUR LOVED ONES... where another photo will go. Add another photo underneath the slogan that you are moving up - GIVE THEM THE GIFT OF KNOWLEDGE
• See the upload section for the new photo
• Do this one exactly like I am asking for and then you can show me some of your ideas. Thanks
• THE PHOTOS UPLOADED ARE EXAMPLES. FEEL FREE TO SEARCH OUT YOUR OWN HIGH RESOLUTION PHOTOS. THANKS

```html
<!DOCTYPE html>
<html lang="en">
<head>
<meta charset="utf-8">
<title>Hereditary Cancer Screening – Exhibit Backdrop</title>
<link href="https://fonts.googleapis.com/css2?family=Montserrat:wght@400;600;700&family=Oswald:wght@300;400;500;700&display=swap" rel="stylesheet">
<style>
  :root {
    --navy: #0b1d5c;
    --green: #7dc242;
    --white: #ffffff;
    --warm-a: #c9a288;
    --warm-b: #8a6a58;
    --cool-a: #d9d2c8;
    --cool-b: #9a8c80;
  }
  html, body {
    margin: 0;
    padding: 0;
    width: 1200px;
    height: 1200px;
    overflow: hidden;
    background: var(--white);
  }
  .backdrop { display: block; width: 1200px; height: 1200px; }
  .title-bold { font-family: "Montserrat", sans-serif; font-weight: 700; fill: var(--navy); }
  .title-light { font-family: "Montserrat", sans-serif; font-weight: 400; fill: var(--navy); }
  .tagline { font-family: "Montserrat", sans-serif; font-weight: 600; fill: var(--white); }
  .headline { font-family: "Oswald", sans-serif; fill: var(--navy); }
  .headline .light { font-weight: 300; }
  .headline .strong { font-weight: 700; }
  .headline-regular { font-family: "Oswald", sans-serif; font-weight: 400; fill: var(--navy); }
  .info-band-text { font-family: "Montserrat", sans-serif; font-weight: 700; fill: var(--white); }
  .cancer-word { font-family: "Oswald", sans-serif; font-weight: 500; fill: var(--green); }
  .lives-line { font-family: "Oswald", sans-serif; font-weight: 500; fill: var(--navy); }
  .panel-strong { font-family: "Oswald", sans-serif; font-weight: 500; fill: var(--white); }
  .panel-light { font-family: "Oswald", sans-serif; font-weight: 300; fill: var(--white); }
  .panel-note { font-family: "Montserrat", sans-serif; font-weight: 400; fill: var(--white); }
  .panel-motto { font-family: "Montserrat", sans-serif; font-weight: 600; fill: var(--white); }
  .brand-name { font-family: "Montserrat", sans-serif; font-weight: 600; fill: var(--navy); letter-spacing: 2px; }
  .rule { fill: var(--navy); }
</style>
</head>
<body>
<svg class="backdrop" viewBox="0 0 1200 1200" xmlns="http://www.w3.org/2000/svg">
  <defs>
    <linearGradient id="warmTone" x1="0" y1="0" x2="1" y2="1">
      <stop offset="0" stop-color="#d8b49a"/>
      <stop offset="1" stop-color="#8f6b57"/>
    </linearGradient>
    <linearGradient id="softTone" x1="0" y1="0" x2="1" y2="1">
      <stop offset="0" stop-color="#e6ddd2"/>
      <stop offset="1" stop-color="#a28f80"/>
    </linearGradient>
    <linearGradient id="gardenTone" x1="0" y1="0" x2="1" y2="1">
      <stop offset="0" stop-color="#b9a66a"/>
      <stop offset="1" stop-color="#c99782"/>
    </linearGradient>
    <linearGradient id="panelFade" x1="0" y1="0" x2="0" y2="1">
      <stop offset="0" stop-color="#8d7a78"/>
      <stop offset="0.35" stop-color="#5c5570"/>
      <stop offset="0.6" stop-color="#0b1d5c"/>
      <stop offset="1" stop-color="#0b1d5c"/>
    </linearGradient>
  </defs>

  <!-- Title block -->
  <g class="title-block">
    <text class="title-bold" x="39" y="133" font-size="74" textLength="417" lengthAdjust="spacingAndGlyphs">Hereditary</text>
    <text class="title-light" x="441" y="204" font-size="72" text-anchor="end" textLength="259" lengthAdjust="spacingAndGlyphs">Cancer</text>
    <text class="title-light" x="441" y="260" font-size="72" text-anchor="end" textLength="368" lengthAdjust="spacingAndGlyphs">Screening</text>
    <rect x="37" y="292" width="404" height="36" fill="var(--green)"/>
    <text class="tagline" x="51" y="320" font-size="29" textLength="376" lengthAdjust="spacingAndGlyphs">The Test You Take For Them</text>
  </g>

  <!-- Photo areas -->
  <g class="photo-grid">
    <rect x="478" y="64" width="319" height="230" fill="url(#gardenTone)" role="img" aria-label="Photo of three generations of women smiling together outdoors"/>
    <rect x="480" y="312" width="143" height="139" fill="url(#gardenTone)" role="img" aria-label="Photo of a grandfather hugging his grandson"/>
    <rect x="646" y="312" width="148" height="135" fill="url(#softTone)" role="img" aria-label="Photo of an extended family gathered at home"/>
    <rect x="0" y="379" width="339" height="267" fill="url(#warmTone)" role="img" aria-label="Photo of a laughing grandmother kissed by two grandchildren"/>
    <rect x="0" y="700" width="339" height="270" fill="url(#softTone)" role="img" aria-label="Photo of grandparents sitting with two grandchildren"/>
    <rect x="435" y="1068" width="345" height="130" fill="url(#softTone)" role="img" aria-label="Photo of a family reading together on a sofa"/>
    <rect x="862" y="776" width="163" height="163" fill="url(#warmTone)" role="img" aria-label="Photo of a grandfather with his granddaughter"/>
    <rect x="1033" y="776" width="162" height="163" fill="url(#softTone)" role="img" aria-label="Photo of a grandmother hugged by her granddaughter"/>
    <rect x="862" y="962" width="163" height="164" fill="url(#softTone)" role="img" aria-label="Photo of grandparents and a grandchild relaxing outdoors"/>
    <rect x="1033" y="962" width="162" height="164" fill="url(#gardenTone)" role="img" aria-label="Photo of a grandmother with young grandchildren in a garden"/>
  </g>

  <!-- Knowledge panel -->
  <g class="knowledge-panel">
    <rect x="859" y="64" width="338" height="673" fill="url(#panelFade)" role="img" aria-label="Photo of a grandmother embracing her granddaughter fading into navy"/>
    <text class="panel-strong" x="1174" y="493" font-size="66" text-anchor="end" textLength="221" lengthAdjust="spacingAndGlyphs"><tspan font-weight="700">GIVE</tspan><tspan font-weight="300"> THEM</tspan></text>
    <text class="panel-light" x="1174" y="531" font-size="32" text-anchor="end" textLength="169" lengthAdjust="spacingAndGlyphs">THE GIFT OF</text>
    <text class="panel-strong" x="1174" y="611" font-size="70" text-anchor="end" textLength="272" lengthAdjust="spacingAndGlyphs">KNOWLEDGE</text>
    <text class="panel-note" x="1181" y="640" font-size="17" text-anchor="end" textLength="298" lengthAdjust="spacingAndGlyphs">knowing is better than not knowing.</text>
    <text class="panel-motto" x="1174" y="675" font-size="26" text-anchor="end" textLength="276" lengthAdjust="spacingAndGlyphs">Knowledge is Power</text>
  </g>

  <!-- Main message -->
  <g class="main-message">
    <text class="headline" x="364" y="567" font-size="100" textLength="456" lengthAdjust="spacingAndGlyphs"><tspan class="light">WILL YOU </tspan><tspan class="strong">GIVE</tspan></text>
    <text class="headline-regular" x="372" y="658" font-size="84" font-weight="300" textLength="458" lengthAdjust="spacingAndGlyphs" style="font-weight:300">YOUR LOVED ONES</text>
    <rect class="rule" x="364" y="676" width="468" height="73"/>
    <text class="info-band-text" x="376" y="726" font-size="36" textLength="445" lengthAdjust="spacingAndGlyphs">the information to Beat</text>
    <rect class="rule" x="364" y="749" width="10" height="451"/>
    <text class="cancer-word" x="387" y="894" font-size="150" textLength="442" lengthAdjust="spacingAndGlyphs">CANCER</text>
    <text class="lives-line" x="394" y="999" font-size="90" textLength="445" lengthAdjust="spacingAndGlyphs">IN THEIR LIVES?</text>
  </g>

  <!-- Divider -->
  <rect class="rule" x="0" y="1037" width="796" height="6"/>

  <!-- Brand -->
  <g class="brand">
    <circle cx="122" cy="1107" r="38" fill="var(--navy)"/>
    <text class="brand-name" x="180" y="1089" font-size="28">KINWELL</text>
    <text class="brand-name" x="180" y="1119" font-size="28">HEALTH</text>
    <text class="brand-name" x="180" y="1149" font-size="28">GROUP</text>
  </g>
</svg>
</body>
</html>
```